Ferncliff Capital - Website Design

We need a website design for a new commercial real estate company called Ferncliff Capital. We're effectively commercial mortgage brokers connecting real estate investors to lenders. We need a website that is simple (not busy), elegant, professional, and user-friendly. A lot of the users will be in their 50's and less tech savvy, so a stream-lined design is best. The website will serve as a portal for lenders to review new financing opportunities, as well as for real estate investors to review terms from lenders.
Updates
Just uploaded our logo.
Target Market(s)
Commercial real estate investors and lenders
Industry/Entity Type
Real Estate
Number of Pages Required
1 page
Colors
Designer to choose colors to be used in the design.
Look and feel

```html
<!DOCTYPE html>
<html lang="en">
<head>
<meta charset="utf-8">
<title>Ferncliff Capital</title>
<link rel="stylesheet" href="https://fonts.googleapis.com/css2?family=Roboto:wght@300;400;500&display=swap">
<style>
:root{
  --green:#8dc63f;
  --green-dark:#7ab52c;
  --blue:#2a9fd6;
  --ink:#2b2b2b;
  --text:#6b6b6b;
  --muted:#8a8a8a;
  --line:#e3e3e3;
  --soft:#f4f5f7;
  --bar:#555555;
  --white:#ffffff;
}
*{box-sizing:border-box;margin:0;padding:0}
html,body{width:1200px;height:2639px;overflow:hidden}
body{position:relative;background:var(--white);font-family:'Roboto',sans-serif;color:var(--text)}
.abs{position:absolute}

.site-header{position:absolute;left:0;top:0;width:1200px;height:100px;background:var(--white)}
.brand{position:absolute;left:86px;top:34px;font-size:26px;font-weight:400;color:var(--ink);letter-spacing:.5px}
.main-nav{position:absolute;right:86px;top:43px;display:flex;gap:50px;font-size:12px;font-weight:500;color:#444}
.main-nav .active{color:var(--blue)}

.hero{position:absolute;left:0;top:100px;width:1200px;height:537px;
  background:linear-gradient(180deg,#8cb8de 0%,#9fc1dc 18%,#6e7076 30%,#dfe3e6 48%,#5d7d3e 62%,#5e9a2a 80%,#70b236 100%)}
.hero-caption{position:absolute;left:709px;top:352px;width:394px;height:176px;background:rgba(20,20,20,.55);padding:26px 24px}
.hero-caption h1{font-size:29px;font-weight:500;color:var(--white);letter-spacing:.3px}
.hero-caption p{margin-top:16px;font-size:12px;line-height:22px;color:#eee}
.hero-dots{position:absolute;left:574px;top:606px;display:flex;gap:8px}
.hero-dots span{width:15px;height:15px;border:2px solid var(--white);border-radius:50%}
.hero-dots .on{background:var(--green)}

.service{position:absolute;top:665px;width:328px;height:312px;border:1px solid var(--line);text-align:center}
.service svg{position:absolute;left:131px;top:35px}
.service h3{position:absolute;left:0;right:0;top:120px;font-size:17px;font-weight:400}
.service p{position:absolute;left:26px;right:26px;top:154px;font-size:12px;line-height:25px}
.service .btn{position:absolute;left:112px;top:243px;width:105px;height:39px;border:1px solid;font-size:12px;line-height:37px}
.is-green h3,.is-green .btn{color:var(--green);border-color:var(--green)}
.is-blue h3,.is-blue .btn{color:var(--blue);border-color:var(--blue)}

.welcome{position:absolute;left:0;top:1033px;width:1200px;height:406px;background:var(--soft)}
.welcome-photo{position:absolute;left:86px;top:46px;width:444px;height:315px;border:4px solid var(--white);box-shadow:0 0 3px rgba(0,0,0,.15);
  background:linear-gradient(135deg,#c7d3da 0%,#6f7a82 40%,#e9e2d5 65%,#86a46a 100%)}
.welcome h2{position:absolute;left:575px;top:51px;font-size:21px;font-weight:400;color:var(--green)}
.welcome .lead{position:absolute;left:578px;top:95px;width:500px;font-size:12px;line-height:25px}
.ticks{position:absolute;left:578px;top:190px;list-style:none;font-size:12px}
.ticks li{height:41px;display:flex;align-items:flex-start;gap:18px}

.cta{position:absolute;left:0;top:1441px;width:1200px;height:357px;background:linear-gradient(180deg,#93cc45,#8ac23c);text-align:center;color:var(--white)}
.cta h2{position:absolute;left:0;right:0;top:73px;font-size:29px;font-weight:500}
.cta h3{position:absolute;left:0;right:0;top:117px;font-size:22px;font-weight:400}
.cta p{position:absolute;left:240px;right:240px;top:167px;font-size:12px;line-height:26px}
.cta .btn{position:absolute;left:493px;top:245px;width:213px;height:45px;border:1px solid rgba(255,255,255,.8);border-radius:3px;font-size:13px;line-height:43px}

.blog-title{position:absolute;left:0;right:0;top:1829px;text-align:center;font-size:21px;font-weight:400;color:var(--green)}
.blog-sub{position:absolute;left:0;right:0;top:1876px;text-align:center;font-size:12px}
.post{position:absolute;top:1921px;width:328px}
.post .thumb{height:197px}
.post h4{margin-top:25px;font-size:16px;font-weight:400;color:var(--ink)}
.post p{margin-top:14px;font-size:12px;line-height:24px}
.post .meta{margin-top:10px;font-size:12px;color:var(--green);display:flex;gap:18px;align-items:center}
.post .meta span{display:flex;gap:6px;align-items:center}

.site-footer{position:absolute;left:0;top:2301px;width:1200px;height:275px;background:var(--soft)}
.map{position:absolute;left:86px;top:46px;width:282px;height:178px;background:linear-gradient(135deg,#e8e4da,#d6dccd 50%,#e9e6dc)}
.f-col{position:absolute;top:56px}
.f-col h5{font-size:16px;font-weight:400;color:var(--ink)}
.contact-list{list-style:none;margin-top:28px;font-size:12px}
.contact-list li{display:flex;gap:14px;height:29px;align-items:flex-start}
.contact-list a{color:var(--text)}
.f-col .note{margin-top:26px;font-size:12px;line-height:22px;width:190px}
.email-box{margin-top:18px;width:213px;height:32px;border:1px solid #ccc;background:var(--white);font-size:12px;padding:0 14px;line-height:30px;color:#555}
.subscribe{margin-top:10px;width:81px;height:27px;background:var(--green);color:var(--white);font-size:11px;font-weight:500;text-align:center;line-height:27px}
.socials{margin-top:18px;display:flex;gap:9px}
.socials span{width:35px;height:35px;border:1px solid #bbb;border-radius:50%}

.copyright{position:absolute;left:0;top:2576px;width:1200px;height:63px;background:var(--bar);color:#eee;font-size:12px;text-align:center;line-height:63px}
</style>
</head>
<body>

<header class="site-header">
  <div class="brand">FERNCLIFF CAPITAL</div>
  <nav class="main-nav">
    <span class="active">HOME</span><span>ABOUT US</span><span>SERVICES</span><span>PROJECTS</span><span>NEWS</span><span>CONTACT US</span>
  </nav>
</header>

<section class="hero" role="img" aria-label="White two-storey house with green lawn and flowering garden">
  <div class="hero-caption">
    <h1>FERNCLIFF CAPITAL</h1>
    <p>Sed ut perspiciatis unde omnis iste natus error sit voluptatem accusantium doloremque laudantium, totam rem aperiam, eaque ipsa quae ab illo inventore dicta sunt explicabo.</p>
  </div>
  <div class="hero-dots"><span></span><span class="on"></span><span></span></div>
</section>

<div class="service is-green" style="left:84px">
  <svg width="66" height="66" viewBox="0 0 66 66" fill="var(--green)"><rect x="16" y="6" width="34" height="56"/><rect x="8" y="58" width="50" height="6"/><g fill="#fff"><rect x="22" y="14" width="6" height="8"/><rect x="38" y="14" width="6" height="8"/><rect x="22" y="28" width="6" height="8"/><rect x="38" y="28" width="6" height="8"/><rect x="22" y="42" width="6" height="8"/><rect x="38" y="42" width="6" height="8"/></g></svg>
  <h3>COMMERCIAL</h3>
  <p>Sed ut perspiciatis unde omnis iste natus error sit voluptatem accusantium doloremque laudantium, eaque ipsa quae ab illo inventore</p>
  <div class="btn">READ MORE</div>
</div>
<div class="service is-blue" style="left:435px">
  <svg width="66" height="66" viewBox="0 0 66 66" fill="var(--blue)"><path d="M4 32 L30 8 L56 32 L50 32 L50 56 L10 56 L10 32 Z"/><circle cx="46" cy="40" r="9" fill="#1c7fb0"/><path d="M32 64 Q46 46 62 64 Z" fill="#1c7fb0"/></svg>
  <h3>MORTGAGE BROKERS</h3>
  <p>Sed ut perspiciatis unde omnis iste natus error sit voluptatem accusantium doloremque laudantium, eaque ipsa quae ab illo inventore</p>
  <div class="btn">READ MORE</div>
</div>
<div class="service is-green" style="left:785px">
  <svg width="66" height="66" viewBox="0 0 66 66"><rect x="8" y="20" width="22" height="40" rx="4" fill="var(--green)"/><circle cx="19" cy="10" r="8" fill="var(--green)"/><circle cx="42" cy="42" r="20" fill="var(--green)"/><text x="42" y="51" text-anchor="middle" font-family="Roboto,sans-serif" font-size="26" font-weight="500" fill="#fff">$</text></svg>
  <h3>INVESTORS TO LENDERS</h3>
  <p>Sed ut perspiciatis unde omnis iste natus error sit voluptatem accusantium doloremque laudantium, eaque ipsa quae ab illo inventore</p>
  <div class="btn">READ MORE</div>
</div>

<section class="welcome">
  <div class="welcome-photo" role="img" aria-label="Agent showing a tablet to a couple outside a house"></div>
  <h2>WELCOME TO FERNCLIFF CAPITAL</h2>
  <p class="lead">Sed ut perspiciatis unde omnis iste natus error sit voluptatem accusantium doloremque lauda ntium, totam rem aperiam, eaque ipsa quae ab illo inventore veritatis et quasi arch ecto beatae vitae dicta sunt explicabo.</p>
  <ul class="ticks">
    <li><svg width="12" height="12" viewBox="0 0 12 12"><path d="M1 6 L4.5 9.5 L11 2.5" fill="none" stroke="var(--green)" stroke-width="2"/></svg>Sed ut perspiciatis unde omnis iste natus error sit</li>
    <li><svg width="12" height="12" viewBox="0 0 12 12"><path d="M1 6 L4.5 9.5 L11 2.5" fill="none" stroke="var(--green)" stroke-width="2"/></svg>voluptatem accusantium doloremque lauda ntium,</li>
    <li><svg width="12" height="12" viewBox="0 0 12 12"><path d="M1 6 L4.5 9.5 L11 2.5" fill="none" stroke="var(--green)" stroke-width="2"/></svg>totam rem aperiam, eaque ipsa quae ab illo inventore</li>
    <li><svg width="12" height="12" viewBox="0 0 12 12"><path d="M1 6 L4.5 9.5 L11 2.5" fill="none" stroke="var(--green)" stroke-width="2"/></svg>veritatis et quasi arch ecto beatae vitae dicta sunt explicabo.</li>
  </ul>
</section>

<section class="cta">
  <h2>COMMERCIAL MORTGAGE BROKERS CONNECTING</h2>
  <h3>REAL ESTATE INVESTORS TO LENDERS</h3>
  <p>Sed ut perspiciatis unde omnis iste natus error sit voluptatem accusantium doloremque lauda ntium, totam rem aperiam, eaque ipsa quae ab illo inventore veritatis et quasi arch ecto beatae vitae dicta sunt explicabo.</p>
  <div class="btn">CLICK HERE FOR MORE INFO</div>
</section>

<h2 class="blog-title">LATEST BLOG</h2>
<p class="blog-sub">Sed ut perspiciatis unde omnis iste natus error sit voluptatem accusantium doloremque laudantium, totam rem aperiam, eaque ipsa</p>

<article class="post" style="left:86px">
  <div class="thumb" role="img" aria-label="Glass office building under blue sky" style="background:linear-gradient(180deg,#6fa3d8,#9bb4c8 50%,#55683e)"></div>
  <h4>NEQUE PORRO QUISQUAM</h4>
  <p>Sed ut perspiciatis unde omnis iste natus error sit voluptatem accusantiumue ipsa beatae vitae dicta sunt explicabo.</p>
  <div class="meta"><span><svg width="12" height="12" viewBox="0 0 12 12" fill="none" stroke="var(--green)"><rect x="1" y="2" width="10" height="9"/><path d="M1 5h10"/></svg>1 month ago</span><span><svg width="13" height="12" viewBox="0 0 13 12" fill="none" stroke="var(--green)"><ellipse cx="6.5" cy="5.5" rx="5.5" ry="4.5"/></svg>05 Comments</span></div>
</article>
<article class="post" style="left:435px">
  <div class="thumb" role="img" aria-label="Hands passing house keys over a signed contract" style="background:linear-gradient(135deg,#5a4a40,#c9b6a3 45%,#e7e2dc 70%,#4a3e36)"></div>
  <h4>NEQUE PORRO QUISQUAM</h4>
  <p>Sed ut perspiciatis unde omnis iste natus error sit voluptatem accusantiumue ipsa beatae vitae dicta sunt explicabo.</p>
  <div class="meta"><span><svg width="12" height="12" viewBox="0 0 12 12" fill="none" stroke="var(--green)"><rect x="1" y="2" width="10" height="9"/><path d="M1 5h10"/></svg>1 month ago</span><span><svg width="13" height="12" viewBox="0 0 13 12" fill="none" stroke="var(--green)"><ellipse cx="6.5" cy="5.5" rx="5.5" ry="4.5"/></svg>05 Comments</span></div>
</article>
<article class="post" style="left:785px">
  <div class="thumb" role="img" aria-label="Stacks of coins in front of a small model house" style="background:linear-gradient(180deg,#2e2218,#8a5a32 55%,#c9863e)"></div>
  <h4>NEQUE PORRO QUISQUAM</h4>
  <p>Sed ut perspiciatis unde omnis iste natus error sit voluptatem accusantiumue ipsa beatae vitae dicta sunt explicabo.</p>
  <div class="meta"><span><svg width="12" height="12" viewBox="0 0 12 12" fill="none" stroke="var(--green)"><rect x="1" y="2" width="10" height="9"/><path d="M1 5h10"/></svg>1 month ago</span><span><svg width="13" height="12" viewBox="0 0 13 12" fill="none" stroke="var(--green)"><ellipse cx="6.5" cy="5.5" rx="5.5" ry="4.5"/></svg>05 Comments</span></div>
</article>

<footer class="site-footer">
  <div class="map" role="img" aria-label="Street map showing the office location"></div>
  <div class="f-col" style="left:412px">
    <h5>CONTACT US</h5>
    <ul class="contact-list">
      <li><svg width="12" height="12" viewBox="0 0 12 12" fill="#777"><path d="M1 4 Q6 0 11 4 L9 6 L7 4.5 L5 4.5 L3 6 Z"/><rect x="2" y="7" width="8" height="4"/></svg>(000)-121-1231 (Phone)</li>
      <li><svg width="12" height="12" viewBox="0 0 12 12" fill="#777"><rect x="3" y="1" width="6" height="4"/><rect x="1" y="5" width="10" height="5"/></svg>(000)-121-1231 (Fax)</li>
      <li><svg width="12" height="12" viewBox="0 0 12 12" fill="none" stroke="#777"><rect x="1" y="2.5" width="10" height="7"/><path d="M1 2.5 L6 7 L11 2.5"/></svg><a>info@ferncliffcapital.com</a></li>
      <li><svg width="12" height="13" viewBox="0 0 12 13" fill="#777"><path d="M6 0 A4.5 4.5 0 0 1 10.5 4.5 C10.5 8 6 13 6 13 C6 13 1.5 8 1.5 4.5 A4.5 4.5 0 0 1 6 0 Z"/><circle cx="6" cy="4.5" r="1.6" fill="#f4f5f7"/></svg><span style="line-height:18px;margin-top:-3px">70 Lorem Ipsum Dummy Text<br>Lorem Ipsum</span></li>
    </ul>
  </div>
  <div class="f-col" style="left:640px">
    <h5>NEWSLETTER</h5>
    <p class="note">Register Your email address to get information ablout us</p>
    <div class="email-box">Email Address</div>
    <div class="subscribe">SUBSCRIBE</div>
  </div>
  <div class="f-col" style="left:894px">
    <h5>FOLLOW US</h5>
    <p class="note">Lorem ipsum dolor sit amet, conse ctetur adipiscing elit. Nulla in purus nibh. Donec ornare</p>
    <div class="socials"><span></span><span></span><span></span><span></span><span></span></div>
  </div>
</footer>

<div class="copyright">© Copyright 2017 Ferncliff Capital All Rights Reserved</div>

</body>
</html>
```